Newspaper Ad (Merry Christmas and Happy New Year)

Hello there,

Firstly, thank you for your interest. I look forward to being inspired by your creativity. I have created a small brief below.

Objective: Create a newspaper ad for our distribution company, Coral Bay Mercantile Limited.

Key message (in priority):
1) To wish everyone a Merry Christmas and Happy New Year.
2) Thanking all our customers
3) Indirectly in a subtle and succinct way you may refer to product/group without it coming as an advertisement.

Size of newspaper ad: 37cm x 26cm - Height x Width. Colour is possible.

More company info: go to our website www.cbmsupply.example. See our company logo (see attachments).

Target Market(s)

Public, clients, potential clients...

Requirements
Must have
• -Merry Christmas and happy new year
• -Indirectly in a subtle and succinct way you may refer to product/group without it coming as an advertisement.
• e.g. Easy Sourcing. Quality Products. Great Service.
• -Mention what we do: Healthcare, Built Environment, Home & Decor, Engineering, Speciality Vehicles, Entrepreneurial
• -contact details:
• CBM Haus, Kestrel Ridge HW, Warato, P.O. Box 7284, Boroko, N.C.D, Papua New Guinea
• T: (+675) 418 2936         F: (+675) 418 2937    

• E: sales@cbmsupply.example      W: www.cbmsupply.example
Nice to have
• -a short message thanking our customers
• -using our CBM logo colour
• -Christmas theme colours (red and green)
Should not have
• -Do not change the colour of our CBM logo

```html
<!DOCTYPE html>
<html lang="en">
<head>
<meta charset="utf-8">
<title>Season's Greetings – Coral Bay Mercantile Limited</title>
<link rel="stylesheet" href="https://fonts.googleapis.com/css2?family=Cinzel:wght@400;700&family=Source+Sans+3:wght@400;600&family=Pinyon+Script&display=swap">
<style>
  :root {
    --card-green: #008c36;
    --ink-white: #ffffff;
    --ink-soft: rgba(255, 255, 255, 0.9);
    --gold-light: #f3d27a;
    --gold-mid: #d9a53a;
    --gold-deep: #b7791f;
    --rule-white: rgba(255, 255, 255, 0.85);
  }
  * { margin: 0; padding: 0; box-sizing: border-box; }
  html, body {
    width: 922px;
    height: 1200px;
    overflow: hidden;
    background: var(--card-green);
  }
  .greeting-card {
    position: relative;
    width: 922px;
    height: 1200px;
    background: var(--card-green);
    color: var(--ink-white);
  }
  .centered {
    position: absolute;
    left: 0;
    width: 100%;
    text-align: center;
  }
  .eyebrow {
    top: 30px;
    font-family: "Source Sans 3", sans-serif;
    font-size: 29px;
    line-height: 1.2;
    letter-spacing: 0.5px;
  }
  .eyebrow-dots {
    position: absolute;
    top: 74px;
    left: 276px;
    width: 370px;
    height: 3px;
    background-image: radial-gradient(circle, var(--gold-mid) 1.2px, transparent 1.4px);
    background-size: 6px 3px;
  }
  .headline {
    font-family: "Cinzel", serif;
    font-weight: 400;
    font-size: 74px;
    line-height: 1;
    letter-spacing: 1px;
  }
  .headline-merry { top: 92px; }
  .headline-christmas { top: 170px; }
  .rule {
    position: absolute;
    height: 2px;
    background: var(--rule-white);
  }
  .rule-merry-left { top: 132px; left: 222px; width: 72px; }
  .rule-merry-right { top: 132px; left: 628px; width: 72px; }
  .tree-art {
    position: absolute;
    top: 275px;
    left: 344px;
    width: 234px;
    height: 305px;
    clip-path: polygon(50% 0, 100% 100%, 0 100%);
    background: linear-gradient(180deg, rgba(255,255,255,0.75), rgba(255,255,255,0.45));
  }
  .new-year {
    font-family: "Pinyon Script", cursive;
    line-height: 1;
    background: linear-gradient(100deg, var(--gold-deep) 30%, var(--gold-light) 50%, var(--gold-mid) 70%);
    -webkit-background-clip: text;
    background-clip: text;
    color: transparent;
  }
  .new-year-happy { top: 596px; font-size: 84px; padding-left: 20px; }
  .new-year-line { top: 680px; font-size: 88px; padding-left: 10px; }
  .thanks {
    top: 820px;
    font-family: "Pinyon Script", cursive;
    font-size: 46px;
    line-height: 1;
  }
  .rule-thanks-left { top: 846px; left: 248px; width: 94px; }
  .rule-thanks-right { top: 846px; left: 580px; width: 94px; }
  .thanks-message {
    top: 884px;
    font-family: "Source Sans 3", sans-serif;
    font-size: 17px;
    line-height: 1.3;
    color: var(--ink-soft);
  }
  .company-name {
    top: 930px;
    font-family: "Cinzel", serif;
    font-weight: 700;
    font-size: 26px;
    line-height: 1.2;
    letter-spacing: 1px;
  }
  .tagline {
    top: 970px;
    font-family: "Source Sans 3", sans-serif;
    font-weight: 600;
    font-size: 17px;
    line-height: 1.3;
    letter-spacing: 1.5px;
    color: var(--gold-light);
  }
  .business-areas {
    top: 1004px;
    font-family: "Source Sans 3", sans-serif;
    font-size: 15px;
    line-height: 1.3;
    color: var(--ink-soft);
  }
  .contact {
    font-family: "Source Sans 3", sans-serif;
    font-size: 15px;
    line-height: 1.3;
    color: var(--ink-soft);
  }
  .contact-address { top: 1050px; }
  .contact-lines { top: 1074px; word-spacing: 2px; }
  .contact-lines span + span { margin-left: 22px; }
  .site-footer {
    position: absolute;
    top: 1140px;
    left: 0;
    width: 100%;
    display: flex;
    align-items: center;
    gap: 12px;
  }
  .footer-rule {
    flex: 1;
    height: 1px;
    background: var(--rule-white);
  }
  .web-icon { width: 28px; height: 28px; flex: none; }
  .web-address {
    font-family: "Source Sans 3", sans-serif;
    font-size: 22px;
    line-height: 30px;
    flex: none;
  }
</style>
</head>
<body>
  <main class="greeting-card">
    <p class="centered eyebrow">We Wish You</p>
    <div class="eyebrow-dots"></div>

    <div class="rule rule-merry-left"></div>
    <h1 class="centered headline headline-merry">Merry</h1>
    <div class="rule rule-merry-right"></div>
    <p class="centered headline headline-christmas">Christmas</p>

    <div class="tree-art" role="img" aria-label="Christmas tree formed from white stars"></div>

    <p class="centered new-year new-year-happy">Happy</p>
    <p class="centered new-year new-year-line">New Year</p>

    <div class="rule rule-thanks-left"></div>
    <p class="centered thanks">Thank You</p>
    <div class="rule rule-thanks-right"></div>
    <p class="centered thanks-message">To all our valued customers – thank you for your trust and support this year.</p>

    <p class="centered company-name">Coral Bay Mercantile Limited</p>
    <p class="centered tagline">Easy Sourcing. Quality Products. Great Service.</p>
    <p class="centered business-areas">Healthcare &nbsp;|&nbsp; Built Environment &nbsp;|&nbsp; Home &amp; Decor &nbsp;|&nbsp; Engineering &nbsp;|&nbsp; Speciality Vehicles &nbsp;|&nbsp; Entrepreneurial</p>

    <p class="centered contact contact-address">CBM Haus, Kestrel Ridge HW, Warato, P.O. Box 7284, Boroko, N.C.D, Papua New Guinea</p>
    <p class="centered contact contact-lines"><span>T: (+675) 418 2936</span><span>F: (+675) 418 2937</span><span>E: sales@cbmsupply.example</span></p>

    <footer class="site-footer">
      <div class="footer-rule"></div>
      <svg class="web-icon" viewBox="0 0 28 28" aria-hidden="true">
        <circle cx="14" cy="14" r="13" fill="none" stroke="#fff" stroke-width="1.2"/>
        <circle cx="14" cy="14" r="8" fill="none" stroke="#fff" stroke-width="1.2"/>
        <ellipse cx="14" cy="14" rx="3.5" ry="8" fill="none" stroke="#fff" stroke-width="1"/>
        <line x1="6" y1="14" x2="22" y2="14" stroke="#fff" stroke-width="1"/>
        <line x1="7.5" y1="10" x2="20.5" y2="10" stroke="#fff" stroke-width="1"/>
        <line x1="7.5" y1="18" x2="20.5" y2="18" stroke="#fff" stroke-width="1"/>
      </svg>
      <p class="web-address">www.cbmsupply.example</p>
      <div class="footer-rule"></div>
    </footer>
  </main>
</body>
</html>
```